Flat bootstrap design for existing site

I'm looking for a modern flat design based around an existing logo. This has to be a custom design (no external templates), and implemented into a bootstrap framework.

The logo is attached as 2 versions - choose whichever you want, that flows better with whatever design you choose.

Added screenshots of the existing site (currently using the default bootstrap layouts). Please make your designs around those pages in the screenshots (i.e. the homepage only has the postal code input and the header). The active page has 3 screenshots, because I wanted to illustrate the other states that would be visible (in the table rows).

This is a moving/junk removal website, just for some context.

Here's some example websites (flat designs) that I like, just to give you an idea of what I'm after.

https://www.plimvora.com/
https://dacklow.com/
https://trevanu.com/
https://quobrintal.com/en/

Coding

Coded - Design and coding required

Number of Pages Required

5+ page

Colors

Designer to choose colors to be used in the design.

Requirements
Must have
• It must be a modern/simple flat design, that is built around the existing logo (attached).
• It has to be implemented using bootstrap.

```html
<!DOCTYPE html>
<html lang="en">
<head>
<meta charset="utf-8">
<title>Bravolt — Junk Removal</title>
<link rel="stylesheet" href="https://fonts.googleapis.com/css2?family=Open+Sans:wght@400;600;800&family=Roboto+Condensed:wght@400&display=swap">
<style>
  :root {
    --sky-light: #6ccbf0;
    --sky-mid: #45b6e6;
    --sky-deep: #3296cf;
    --white: #ffffff;
    --panel-head: #f5f5f5;
    --panel-line: #dcdcdc;
    --ink: #3a3a3a;
    --muted: #555555;
    --button: #4ac8f5;
    --footer: #363636;
  }
  * { box-sizing: border-box; margin: 0; padding: 0; }
  html, body { width: 1200px; height: 742px; overflow: hidden; }
  body { position: relative; font-family: "Open Sans", Arial, sans-serif; background: var(--footer); }

  .hero-backdrop {
    position: absolute; left: 0; top: 0; width: 1200px; height: 620px;
    background: linear-gradient(120deg, var(--sky-light) 0%, var(--sky-mid) 45%, var(--sky-deep) 100%);
  }

  .site-header { position: absolute; left: 0; top: 0; width: 1200px; height: 120px; }
  .brand {
    position: absolute; left: 98px; top: 40px;
    display: flex; align-items: center; gap: 10px;
    color: var(--white); font-weight: 800; font-size: 40px; letter-spacing: 1px;
    text-decoration: none;
  }
  .brand-dot { width: 22px; height: 22px; border-radius: 50%; background: var(--white); }

  .main-nav { position: absolute; right: 99px; top: 41px; display: flex; align-items: center; gap: 18px; }
  .main-nav a {
    color: var(--white); text-decoration: none; font-weight: 600; font-size: 14px;
    line-height: 33px; padding: 0 0;
  }
  .main-nav a + a { margin-left: 0; }
  .main-nav .nav-cta {
    border: 2px solid var(--white); border-radius: 18px; padding: 0 16px; line-height: 31px;
  }

  .booking-panel {
    position: absolute; left: 98px; top: 147px; width: 1003px; height: 403px;
    background: var(--white); border-radius: 3px; box-shadow: 0 2px 6px rgba(0,0,0,.18);
    overflow: hidden;
  }
  .booking-panel-head {
    height: 115px; background: var(--panel-head); border-bottom: 1px solid var(--panel-line);
    display: flex; align-items: center; justify-content: center;
  }
  .booking-title {
    font-family: "Roboto Condensed", "Arial Narrow", sans-serif; font-weight: 400;
    font-size: 31px; color: var(--ink); letter-spacing: .3px;
  }
  .booking-form { position: relative; height: 288px; }
  .postal-input {
    position: absolute; left: 241px; top: 86px; width: 522px; height: 47px;
    border: 1px solid var(--panel-line); border-radius: 2px;
    box-shadow: inset 0 3px 4px rgba(0,0,0,.06);
    font-family: "Open Sans", Arial, sans-serif; font-size: 11px; text-align: center; color: var(--muted);
  }
  .postal-input::placeholder { color: var(--muted); }
  .book-button {
    position: absolute; left: 438px; top: 160px; width: 129px; height: 34px;
    background: var(--button); border: 0; border-radius: 2px; color: var(--white);
    font-family: "Open Sans", Arial, sans-serif; font-size: 19px;
  }

  .site-footer {
    position: absolute; left: 0; top: 620px; width: 1200px; height: 122px;
    background: var(--footer); text-align: center; color: var(--white);
  }
  .copyright { margin-top: 37px; font-size: 11px; font-weight: 600; }
  .social-links { margin-top: 13px; display: flex; justify-content: center; gap: 4px; }
  .social-links a {
    width: 24px; height: 24px; border: 1.5px solid #e6e6e6; border-radius: 50%; display: block;
  }
</style>
</head>
<body>
  <div class="hero-backdrop" role="img" aria-label="Soft blue low-poly geometric background"></div>

  <header class="site-header">
    <a class="brand" href="#"><span class="brand-dot"></span>BRAVOLT</a>
    <nav class="main-nav">
      <a href="#">BOOK</a>
      <a href="#">HOW IT WORKS</a>
      <a class="nav-cta" href="#">BECOME A DRIVER</a>
      <a href="#">SIGN IN</a>
    </nav>
  </header>

  <main class="booking-panel">
    <div class="booking-panel-head">
      <h1 class="booking-title">NEED JUNK REMOVED? BOOK NOW.</h1>
    </div>
    <form class="booking-form">
      <input class="postal-input" type="text" placeholder="Postal code" aria-label="Postal code">
      <button class="book-button" type="button">Book</button>
    </form>
  </main>

  <footer class="site-footer">
    <p class="copyright">©2017 BRAVOLT, ALL RIGHTS RESERVED.</p>
    <div class="social-links">
      <a href="#" aria-label="Social link"></a>
      <a href="#" aria-label="Social link"></a>
      <a href="#" aria-label="Social link"></a>
      <a href="#" aria-label="Social link"></a>
      <a href="#" aria-label="Social link"></a>
    </div>
  </footer>
</body>
</html>
```